Sparrow Haulage needs a business card design.

Design a double-sided business card for new freight business. On the front, would like to see our logo along with the following info:

Martin Obuya
CEO/FOUNDER
555-206-7142
martinobuya@sparrow-haulage.example

On the reverse side, we would like to use the graphic image of our logo only without the Sparrow Haulage name.

```html
<!DOCTYPE html>
<html lang="en">
<head>
<meta charset="utf-8">
<title>Sparrow Haulage — Business Card</title>
<link href="https://fonts.googleapis.com/css2?family=Montserrat:wght@500;700;800&display=swap" rel="stylesheet">
<style>
  :root {
    --navy: #1b1957;
    --red: #b81c26;
    --paper: #ffffff;
    --pattern-light: #f4f4f4;
    --pattern-mid: #e4e4e4;
    --backdrop: #ecebe8;
  }
  * { box-sizing: border-box; margin: 0; padding: 0; }
  html, body {
    width: 1200px; height: 900px; overflow: hidden;
    background: var(--backdrop);
    font-family: "Montserrat", Arial, sans-serif;
  }
  .sheet {
    position: relative; width: 1200px; height: 900px;
    display: flex; flex-direction: column; align-items: center; justify-content: center; gap: 44px;
  }
  .card {
    position: relative; width: 580px; height: 330px;
    background: var(--paper); border-radius: 10px; overflow: hidden;
    box-shadow: 0 2px 10px rgba(0,0,0,0.12);
  }
  /* Reverse side: brand symbol only, no name */
  .card-back .pattern-field {
    position: absolute; inset: 0;
    background: linear-gradient(100deg, var(--pattern-mid) 0%, var(--pattern-light) 60%, var(--paper) 100%);
  }
  .card-back .back-symbol {
    position: absolute; left: 408px; top: 207px;
    width: 54px; height: 54px; background: var(--navy);
  }
  /* Front side */
  .brand {
    position: absolute; left: 22px; top: 32px;
    display: flex; align-items: center; gap: 22px;
  }
  .brand-square { width: 100px; height: 100px; background: var(--navy); }
  .brand-name {
    font-weight: 800; font-size: 44px; line-height: 1.05; letter-spacing: 5px;
    color: var(--navy); text-transform: uppercase;
  }
  .contact-row {
    position: absolute; left: 20px; top: 198px; right: 20px;
    display: flex; align-items: center;
  }
  .person { text-align: right; }
  .person-name { font-weight: 800; font-size: 18px; color: var(--navy); }
  .person-title { font-weight: 500; font-size: 15px; color: var(--red); margin-top: 2px; }
  .divider-square { width: 34px; height: 34px; background: var(--navy); margin: 0 18px 0 16px; flex: none; }
  .details { list-style: none; }
  .details li {
    display: flex; align-items: center; gap: 8px;
    font-weight: 500; font-size: 15.5px; color: var(--navy); line-height: 1.5;
    white-space: nowrap;
  }
  .details svg { width: 13px; height: 13px; fill: var(--red); flex: none; }
  .rule-red {
    position: absolute; left: 0; right: 0; bottom: 51px; height: 4px; background: var(--red);
  }
  .band-navy {
    position: absolute; left: 0; right: 0; bottom: 0; height: 51px; background: var(--navy);
  }
</style>
</head>
<body>
<main class="sheet">
  <section class="card card-back" aria-label="Business card reverse">
    <div class="pattern-field" role="img" aria-label="Faint repeating brand pattern in light grey"></div>
    <div class="back-symbol" aria-hidden="true"></div>
  </section>

  <section class="card card-front" aria-label="Business card front">
    <div class="brand">
      <div class="brand-square"></div>
      <div class="brand-name">Sparrow<br>Haulage</div>
    </div>

    <div class="contact-row">
      <div class="person">
        <div class="person-name">Martin Obuya</div>
        <div class="person-title">CEO/FOUNDER</div>
      </div>
      <div class="divider-square"></div>
      <ul class="details">
        <li>
          <svg viewBox="0 0 16 16" aria-hidden="true"><path d="M1 5c0-2 3-3 7-3s7 1 7 3v1.5h-3.5V5H4.5v1.5H1zM3 8l2-2h6l2 2v6H3zm5 1.2a1.8 1.8 0 1 0 0 3.6 1.8 1.8 0 0 0 0-3.6z"/></svg>
          555-206-7142
        </li>
        <li>
          <svg viewBox="0 0 16 16" aria-hidden="true"><path d="M1 3h14v10H1zm1.5 1.5v.4L8 9l5.5-4.1v-.4zm0 2.2v4.8h11V6.7L8 10.8z"/></svg>
          martinobuya@sparrow-haulage.example
        </li>
      </ul>
    </div>

    <div class="rule-red"></div>
    <div class="band-navy"></div>
  </section>
</main>
</body>
</html>
```